Stationary design for boutique production house

We need a stationary design for our production house, 'Lorno Productions' based in Singapore. We produce microfilms as well as podcasts, talkshows and events. Our logo is a stylized icon of our director, who is also the executive producer and host of our programs, Lorno. Our main company colors are Red, Black and white. We would like a clean, minimalist design incorporating our existing company logo that conveys a sense of urbanism and elegance.

Logo and font files are attached. f

Target Market(s)

We focus on lifestyle media rather than entertainment.

Industry/Entity Type

Boutique

Font styles to use
Serif
Sans Serif

Colors
ec1f27
ffffff
000000

Requirements
Must have
• Our company logo and at least one of our company colors.
Nice to have
• Our address and contact information.
Should not have
• Changes made to the company logo (using only certain parts of it is fine though)

```html
<!DOCTYPE html>
<html lang="en">
<head>
<meta charset="utf-8">
<title>Lorno Productions — Stationery</title>
<link href="https://fonts.googleapis.com/css2?family=Roboto:wght@400;700&family=Exo+2:wght@500&display=swap" rel="stylesheet">
<style>
:root{
  --red:#e5232b;
  --ink:#333233;
  --paper:#ffffff;
  --ground:#eeeeee;
  --text:#555555;
}
*{margin:0;padding:0;box-sizing:border-box}
html,body{width:1200px;height:937px;overflow:hidden;background:var(--ground);font-family:'Roboto',Arial,sans-serif;color:var(--text)}
.sheet{position:absolute;background:var(--paper);overflow:hidden}
.wave{position:absolute;left:0;bottom:0;width:100%}
.brand{position:absolute;display:flex;align-items:center;gap:.35em;white-space:nowrap}
.brand-dot{flex:none;width:.45em;height:.45em;border-radius:50%;background:var(--red)}
.brand-name{font-family:'Roboto',Arial,sans-serif;font-weight:700;color:var(--ink);line-height:1;letter-spacing:.12em}
.web{position:absolute;color:#fff;font-family:'Exo 2',Arial,sans-serif;letter-spacing:.22em;white-space:nowrap}

/* letterhead */
.letterhead{left:185px;top:68px;width:385px;height:542px}
.letterhead .brand{left:18px;top:108px;font-size:22px}
.contact{position:absolute;right:16px;top:20px;text-align:right;font-size:4.6px;line-height:7px;color:#333}
.contact b{display:block}
.letter{position:absolute;left:36px;top:200px;width:300px;font-size:5px;line-height:7.2px}
.letter p{margin-bottom:9px}
.letter .gap{margin-bottom:22px}
.signature{display:block;width:34px;height:18px;margin:4px 0 6px}

/* folder */
.folder{left:637px;top:41px;width:456px;height:575px}
.folder .brand{left:0;width:100%;justify-content:center;top:330px;font-size:42px}
.folder .web{left:20px;bottom:12px;font-size:10.5px}

/* business cards */
.card-front{left:46px;top:659px;width:175px;height:99px;border-radius:6px}
.card-front .brand{left:10px;top:30px;font-size:11px}
.holder{position:absolute;left:101px;top:14px;font-size:5px;line-height:6px;color:#333}
.holder b{font-size:5.2px;letter-spacing:.04em}
.holder ul{list-style:none;margin-top:5px;font-size:3.6px;line-height:6px}
.card-front .address{position:absolute;left:7px;bottom:8px;color:#fff;font-size:4.4px;line-height:6px;font-weight:700}
.card-back{left:46px;top:785px;width:175px;height:99px;border-radius:6px}
.card-back .brand{left:0;width:100%;justify-content:center;top:42px;font-size:14px}

/* envelopes */
.envelope-front{left:267px;top:672px;width:432px;height:208px}
.envelope-front .brand{left:16px;top:48px;font-size:16px}
.envelope-front .web{left:12px;bottom:10px;font-size:9.5px}
.envelope-back{left:737px;top:672px;width:431px;height:208px}
.flap{position:absolute;left:0;top:0;width:100%;height:72px;background:var(--ink);border-radius:0 0 46px 46px}
.envelope-back .web{left:0;width:100%;top:27px;text-align:center;font-size:12.5px}
</style>
</head>
<body>

<section class="sheet letterhead" aria-label="Letterhead">
  <div class="brand"><span class="brand-dot"></span><span class="brand-name">LORNO</span></div>
  <div class="contact">
    <b>12 Keong Saik Road</b>
    <b>Singapore 089128</b>
    <span>+65 6123 4501</span><br>
    <span>+65 8123 4502</span><br>
    <span>+65 6123 4503</span><br>
    <span>hello@lornostudio.com</span><br>
    <span>www.lornostudio.com</span>
  </div>
  <div class="letter">
    <p>July 2, 2012</p>
    <p><b>Dear Sir,</b><br>Orchid House, Bukit Lane, Singapore</p>
    <p>Thank you for your interest in working with our studio. We produce microfilms, podcasts, talk shows and live events for lifestyle brands across the region. Our small team takes each project from first idea to final cut, with care for story, light and sound. We would be glad to share a short reel of our recent work and to talk through the timeline and budget that suits your plans for the coming season.</p>
    <p class="gap">Please find enclosed our proposal and a summary of the services we offer, along with a draft schedule for the shoot days.</p>
    <p>We look forward to meeting you at our studio. Our producers will prepare a treatment, a shot list and a set of mood boards before the first session, so that every detail is clear well ahead of time. After the shoot we handle editing, colour, sound and delivery in all the formats you need for screens, stages and social channels. If you have any questions, please reach us by phone or email at any time.</p>
    <p>Best Regards,</p>
    <svg class="signature" viewBox="0 0 34 18" aria-hidden="true"><path d="M2 15 C6 2 8 2 7 14 M5 9 L12 8 C14 14 16 6 18 12 S24 8 26 12 S31 10 33 9" fill="none" stroke="#222" stroke-width=".8"/></svg>
    <p><b>Daniel Koh</b><br>Director<br>Orchid House, Bukit Lane, Singapore</p>
  </div>
  <svg class="wave" viewBox="0 0 385 80" height="80" preserveAspectRatio="none" aria-hidden="true">
    <path d="M0 30 C90 6 170 32 250 32 S350 12 385 2 L385 80 L0 80Z" fill="var(--ink)"/>
    <path d="M0 24 C90 0 170 26 250 26 S350 6 385 -4" fill="none" stroke="var(--red)" stroke-width="2.5"/>
    <path d="M0 19 C90 -5 170 21 250 21 S350 1 385 -9" fill="none" stroke="var(--red)" stroke-width="1.2"/>
  </svg>
</section>

<section class="sheet folder" aria-label="Presentation folder">
  <div class="brand"><span class="brand-dot"></span><span class="brand-name">LORNO</span></div>
  <svg class="wave" viewBox="0 0 456 100" height="100" preserveAspectRatio="none" aria-hidden="true">
    <path d="M0 44 C110 10 210 44 300 42 S420 18 456 8 L456 100 L0 100Z" fill="var(--ink)"/>
    <path d="M0 36 C110 2 210 36 300 34 S420 10 456 0" fill="none" stroke="var(--red)" stroke-width="3.5"/>
    <path d="M0 30 C110 -4 210 30 300 28 S420 4 456 -6" fill="none" stroke="var(--red)" stroke-width="1.6"/>
  </svg>
  <div class="web">www.lornostudio.com</div>
</section>

<section class="sheet card-front" aria-label="Business card, front">
  <div class="brand"><span class="brand-dot"></span><span class="brand-name">LORNO</span></div>
  <div class="holder">
    <b>MARCUS TAN</b><br>Managing Director
    <ul>
      <li>+65 6123 4501</li>
      <li>+65 8123 4502</li>
      <li>+65 6123 4503</li>
      <li>hello@lornostudio.com</li>
      <li>www.lornostudio.com</li>
    </ul>
  </div>
  <svg class="wave" viewBox="0 0 175 36" height="36" preserveAspectRatio="none" aria-hidden="true">
    <path d="M0 14 C40 4 80 16 115 14 S160 4 175 0 L175 36 L0 36Z" fill="var(--ink)"/>
    <path d="M0 11 C40 1 80 13 115 11 S160 1 175 -3" fill="none" stroke="var(--red)" stroke-width="1.5"/>
  </svg>
  <div class="address">12 Keong Saik Road<br>Singapore 089128</div>
</section>

<section class="sheet card-back" aria-label="Business card, back">
  <div class="brand"><span class="brand-dot"></span><span class="brand-name">LORNO</span></div>
</section>

<section class="sheet envelope-front" aria-label="Envelope, front">
  <div class="brand"><span class="brand-dot"></span><span class="brand-name">LORNO</span></div>
  <svg class="wave" viewBox="0 0 432 70" height="70" preserveAspectRatio="none" aria-hidden="true">
    <path d="M0 36 C100 10 200 36 290 34 S400 14 432 4 L432 70 L0 70Z" fill="var(--ink)"/>
    <path d="M0 29 C100 3 200 29 290 27 S400 7 432 -3" fill="none" stroke="var(--red)" stroke-width="3"/>
    <path d="M0 24 C100 -2 200 24 290 22 S400 2 432 -8" fill="none" stroke="var(--red)" stroke-width="1.4"/>
  </svg>
  <div class="web">www.lornostudio.com</div>
</section>

<section class="sheet envelope-back" aria-label="Envelope, back">
  <div class="flap"></div>
  <div class="web">www.lornostudio.com</div>
</section>

</body>
</html>
```